Real Estate Brokerage Stationery Designs

I am looking to have presentation folders with business card slots on both sides along with pockets on both sides. I've attached logos, website colors along with current business card designs.

I am looking for envelope designs both big and small. Possibly new business card designs, notepad templates for big and small notepads. Letterhead designs. Pop socket designs. Realtors name badge designs.

www.brightholdrealty.example

```html
<!DOCTYPE html>
<html lang="en">
<head>
<meta charset="utf-8">
<title>Brighthold Realty – Business Card</title>
<link href="https://fonts.googleapis.com/css2?family=PT+Sans:wght@400;700&display=swap" rel="stylesheet">
<style>
  :root {
    --backdrop: #9c9c9c;
    --card: #ffffff;
    --brand-blue: #1b5cb3;
    --text-gray: #555555;
    --text-dark: #2b2b2b;
    --rule: #c4c4c4;
    --badge: #2a2a2a;
  }
  * { box-sizing: border-box; margin: 0; padding: 0; }
  html, body { width: 1133px; height: 1200px; overflow: hidden; }
  body {
    background: var(--backdrop);
    font-family: "PT Sans", Arial, sans-serif;
    position: relative;
  }
  .card {
    position: absolute;
    left: 218px;
    width: 696px;
    height: 397px;
    background: var(--card);
    overflow: hidden;
  }
  .card--front { top: 153px; }
  .card--back { top: 647px; }

  /* Front */
  .brand {
    position: absolute;
    left: 62px;
    top: 170px;
    display: flex;
    align-items: center;
    gap: 10px;
  }
  .brand__mark { width: 16px; height: 16px; background: var(--brand-blue); }
  .brand__name {
    font-size: 30px;
    font-weight: 700;
    color: var(--brand-blue);
    line-height: 1;
  }
  .divider {
    position: absolute;
    left: 315px;
    top: 99px;
    width: 2px;
    height: 185px;
    background: linear-gradient(to bottom, transparent, var(--rule) 20%, var(--rule) 80%, transparent);
  }
  .contact {
    position: absolute;
    left: 348px;
    top: 103px;
    list-style: none;
    color: var(--text-gray);
    font-size: 17px;
    line-height: 22.5px;
  }
  .contact__item { display: flex; align-items: flex-start; }
  .contact__item--address { margin-bottom: 8px; }
  .contact__icon { width: 20px; height: 22px; margin-right: 12px; flex: none; fill: var(--brand-blue); }
  .services {
    position: absolute;
    left: 0;
    width: 100%;
    top: 321px;
    text-align: center;
    color: var(--text-gray);
    font-size: 17px;
    line-height: 23px;
  }
  .services__dot {
    display: inline-block;
    width: 6px; height: 6px;
    background: var(--brand-blue);
    margin: 0 6px;
    vertical-align: middle;
  }

  /* Back */
  .badge { position: absolute; background: var(--badge); }
  .badge--housing { left: 60px; top: 45px; width: 50px; height: 48px; }
  .badge--listing { left: 134px; top: 48px; width: 85px; height: 40px; border: 2px solid var(--badge); background: transparent; }
  .portrait {
    position: absolute;
    left: 312px;
    top: 17px;
    right: 0;
    bottom: 0;
    background: linear-gradient(to bottom, #f3f3f3 0%, #e8e8e8 45%, #6f6f6f 75%, #2a2a2a 100%);
  }
  .agent {
    position: absolute;
    left: 58px;
    top: 282px;
  }
  .agent__name {
    font-size: 31px;
    font-weight: 700;
    color: var(--brand-blue);
    line-height: 34px;
  }
  .agent__title {
    font-size: 25px;
    color: var(--text-dark);
    line-height: 26px;
  }
</style>
</head>
<body>

<section class="card card--front">
  <div class="brand">
    <span class="brand__mark"></span>
    <span class="brand__name">Brighthold Realty</span>
  </div>

  <div class="divider"></div>

  <ul class="contact">
    <li class="contact__item contact__item--address">
      <svg class="contact__icon" viewBox="0 0 20 22"><path d="M10 1a6.5 6.5 0 0 0-6.5 6.5C3.5 12.5 10 20 10 20s6.5-7.5 6.5-12.5A6.5 6.5 0 0 0 10 1zm0 9a2.5 2.5 0 1 1 0-5 2.5 2.5 0 0 1 0 5z"/></svg>
      <span>820 Harborline Ave, Suite 140,<br>Palm Vista, FL 33400</span>
    </li>
    <li class="contact__item">
      <svg class="contact__icon" viewBox="0 0 20 22"><path d="M2 8c0-2 3.5-4 8-4s8 2 8 4v1.5h-4V8H6v1.5H2zM5 11h10l2 7H3z"/></svg>
      <span>555-201-4417</span>
    </li>
    <li class="contact__item">
      <svg class="contact__icon" viewBox="0 0 20 22"><path d="M6 3h8a1 1 0 0 1 1 1v15a1 1 0 0 1-1 1H6a1 1 0 0 1-1-1V4a1 1 0 0 1 1-1zm1 2v11h6V5z"/></svg>
      <span>555-201-8832</span>
    </li>
    <li class="contact__item">
      <svg class="contact__icon" viewBox="0 0 20 22"><path d="M6 3h8v5H6zM2 10h16v7H2zm4 5h8v4H6z"/></svg>
      <span>555-201-6609</span>
    </li>
    <li class="contact__item">
      <svg class="contact__icon" viewBox="0 0 20 22"><path d="M2 7h16v1l-8 5-8-5zm0 3 8 5 8-5v7H2z"/></svg>
      <span>jordan@brightholdrealty.example</span>
    </li>
    <li class="contact__item">
      <svg class="contact__icon" viewBox="0 0 20 22"><circle cx="10" cy="12" r="8"/><path d="M6 8c2 0 3 1 3 3s-2 2-2 4M12 6c0 2 2 2 3 4" stroke="#fff" stroke-width="1.5" fill="none"/></svg>
      <span>www.brightholdrealty.example</span>
    </li>
  </ul>

  <p class="services">
    Residential Real Estate<span class="services__dot"></span>Commercial Real Estate<br>
    Property Management<span class="services__dot"></span>Investments
  </p>
</section>

<section class="card card--back">
  <div class="badge badge--housing"></div>
  <div class="badge badge--listing"></div>

  <div class="portrait" role="img" aria-label="Portrait photo of the broker in a dark suit and tie against a light studio backdrop"></div>

  <div class="agent">
    <h1 class="agent__name">Jordan Avery</h1>
    <p class="agent__title">Broker</p>
  </div>
</section>

</body>
</html>
```